Business card design for modern PanoWalk agency

Hello,

I need a business card design for my company Kites7Market.
We mainly offer Zorvex PanoWalk Tours (360° Photography) and it should be a business card with following details:

Name: Tobias Wendler
Number: +49 176 58 20 917
Mail: tobias@kites7market.com
website: kites7market.com

Main colour that we use is the red of the logo.
It´s also important to integrate the "Zorvex Verified logo" as the person on this business card is a Zorvex verified photographer.

And if possible we would also like to integrate something like send us a sms or whatsapp and we call you back. As the number is german but we sell now in Vienna, Austria.

We offer a good price but very high photography quality, as we are mostly students - that´s our concept.

Maybe an idea is to integrate something 360° on the back-side of the card, for example the photo attached (just an idea) or some great design.
See flyer (attached) and kites7market.com for inspiration, maybe use of the photo of me (attached) in a circle or something

I´m very excited for your designs and thanks a lot in advance!! :)

Target Market(s)

Shops, hotels, shopping centers, etc. in Vienna, Austria

Industry/Entity Type

Business

Contact Information for Business Card

double-sided, use red of the logo, 360° zorvex pano walk certified photographer

Font styles to use
Serif
Sans Serif

Colors
ec1f27

Requirements
Nice to have
• maybe some 360° design on back-side
• maybe include photo of me in a circle or something or sketched in red colour

```html
<!DOCTYPE html>
<html lang="en">
<head>
<meta charset="UTF-8">
<title>Kites7Market – Business Card</title>
<link href="https://fonts.googleapis.com/css2?family=Open+Sans:wght@400;600;700;800&display=swap" rel="stylesheet">
<style>
  :root {
    --brand-red: #ec1f27;
    --ink-black: #231f20;
    --logo-grey: #9d9fa2;
    --text-dark: #2b2b2b;
    --card-white: #ffffff;
    --back-maroon: #6a2b2d;
    --badge-green: #34a853;
    --page-bg: #e9e7e4;
  }
  * { box-sizing: border-box; margin: 0; padding: 0; }
  html, body {
    width: 1200px; height: 900px; overflow: hidden;
    background: var(--page-bg);
    font-family: "Open Sans", Arial, sans-serif;
  }
  .sheet {
    width: 1200px; height: 900px;
    display: flex; flex-direction: column; align-items: center; justify-content: center;
    gap: 36px;
  }
  .card {
    position: relative;
    width: 720px; height: 400px;
    overflow: hidden;
    box-shadow: 0 6px 18px rgba(0,0,0,0.18);
  }

  /* Back side */
  .card-back { background: var(--back-maroon); }
  .tour-tile {
    position: absolute;
    width: 124px; height: 124px;
    border-radius: 18px;
    transform: rotate(45deg);
  }
  .tile-runner {
    left: 108px; top: 46px;
    background: linear-gradient(135deg, #f3d9a4 0%, #d9a35a 55%, #8a6a45 100%);
  }
  .tile-skater {
    left: 308px; top: 128px;
    background: linear-gradient(135deg, #cfe6df 0%, #9fc7c2 45%, #f08a3c 100%);
  }
  .tile-desk {
    left: 508px; top: 210px;
    background: linear-gradient(135deg, #f4f4f2 0%, #dde3e6 55%, #a9b4bb 100%);
  }
  .verified-badge {
    position: absolute;
    left: 128px; top: 300px;
    width: 156px; height: 34px;
    border-radius: 6px;
    background: rgba(255,255,255,0.14);
    display: flex; align-items: center; padding-left: 10px;
  }
  .verified-badge .badge-dot {
    width: 16px; height: 16px; border-radius: 50%;
    background: var(--badge-green);
  }

  /* Front side */
  .card-front { background: var(--card-white); }
  .front-shapes { position: absolute; inset: 0; }
  .holder-name {
    position: absolute; left: 60px; top: 30px;
    font-weight: 700; font-size: 17px;
    color: var(--brand-red);
  }
  .brand-lockup {
    position: absolute; left: 226px; top: 150px;
    display: flex; align-items: center; gap: 14px;
  }
  .brand-square {
    width: 34px; height: 34px;
    background: var(--brand-red);
  }
  .brand-name {
    font-weight: 800; font-size: 44px; letter-spacing: 0.5px;
    color: var(--logo-grey);
    line-height: 1;
  }
  .contact-list {
    position: absolute; left: 38px; top: 246px;
    list-style: none;
  }
  .contact-item {
    display: flex; align-items: center; gap: 10px;
    font-size: 16px; color: var(--text-dark);
    line-height: 24px;
  }
  .contact-icon { width: 13px; height: 13px; flex: none; }
</style>
</head>
<body>
<main class="sheet">

  <section class="card card-back" aria-label="Business card back">
    <div class="tour-tile tile-runner" role="img" aria-label="Photo of running shoes on a sunlit road"></div>
    <div class="tour-tile tile-skater" role="img" aria-label="Photo of a skateboarder in warm evening light"></div>
    <div class="tour-tile tile-desk" role="img" aria-label="Photo of glasses on a bright desk"></div>
    <div class="verified-badge" role="img" aria-label="Verified photographer badge">
      <span class="badge-dot"></span>
    </div>
  </section>

  <section class="card card-front" aria-label="Business card front">
    <svg class="front-shapes" width="720" height="400" viewBox="0 0 720 400" aria-hidden="true">
      <polygon points="0,0 78,0 62,16 0,16" fill="var(--brand-red)"/>
      <polygon points="14,40 58,8 58,40" fill="var(--ink-black)"/>
      <polygon points="0,330 300,342 296,354 0,342" fill="var(--brand-red)"/>
      <polygon points="300,344 720,362 720,400 282,400 296,360" fill="var(--ink-black)"/>
      <polygon points="296,344 306,344 292,362 282,362" fill="var(--brand-red)"/>
    </svg>

    <h1 class="holder-name">Tobias Wendler</h1>

    <div class="brand-lockup">
      <span class="brand-square"></span>
      <span class="brand-name">KITES7MARKET</span>
    </div>

    <ul class="contact-list">
      <li class="contact-item">
        <svg class="contact-icon" viewBox="0 0 12 12"><rect x="3" y="0.5" width="6" height="11" rx="1.2" fill="none" stroke="var(--brand-red)" stroke-width="1.4"/><circle cx="6" cy="9.4" r="0.8" fill="var(--brand-red)"/></svg>
        +49 176 58 20 917
      </li>
      <li class="contact-item">
        <svg class="contact-icon" viewBox="0 0 12 12"><rect x="0.5" y="2" width="11" height="8" fill="var(--brand-red)"/><polyline points="0.5,2 6,6.5 11.5,2" fill="none" stroke="#fff" stroke-width="1"/></svg>
        tobias@kites7market.com
      </li>
      <li class="contact-item">
        <svg class="contact-icon" viewBox="0 0 12 12"><circle cx="6" cy="6" r="5.5" fill="var(--brand-red)"/><ellipse cx="6" cy="6" rx="2.2" ry="5.5" fill="none" stroke="#fff" stroke-width="0.8"/><line x1="0.5" y1="6" x2="11.5" y2="6" stroke="#fff" stroke-width="0.8"/></svg>
        kites7market.com
      </li>
    </ul>
  </section>

</main>
</body>
</html>
```